Dentistry Office

We want a new design for a Dentist's office website.

The theme is: "We provide high quality, state-of-the-art, dental care in a comfortable, caring environment."

The site currently has a menu on the left of the page with about 40 items on it. There is a great deal of textual content on each page, plus several illustrations.

We want to do this using CSS, so we need specifications in the CSS for all possible elements. The CSS needs to be named in a logical manner for easy use.

Every dentist on the planet seems to use lots of Flash. We don't want to because it is so distracting. We are looking for an elegant solution targeting 24-55 age group, but not excluding anyone.

The following (from another dentist's site) can give you a taste of what we want to communicate on the site:

"After 20 years of teaching dentists how to refine their technique and many years of writing textbooks, I currently devote my time to my office and the hands-on practice of dentistry. I'd like to welcome you personally to my dental practice, and I invite you to meet my highly experienced team of professionals.

"We have offered complete dental care of the highest quality since 1978. We provide Preventive Services, Tooth Whitening and Cosmetic Dentistry for a beautiful smile, Endodontics (root canal treatment) to treat painful teeth, Sedation Dentistry so you can relax, and Dental Implants to restore what is missing. We offer total care.

"Our approach to your health is simple: We use our education, experience and dedication to provide every patient with superior dental care.

"This passion for excellence is not just a goal, but a standard every member of our team holds.

"We also pride ourselves with our state of the art procedures, training and technology. This includes creating a beautiful smile using techniques that preserve as much of the original tooth as possible.

"Our abilities are renowned throughout the dental profession and I hope if you have any questions you will contact us by an e-mail note, by phone or just by dropping by."

Keep in mind the screen shape and dimensions. Your design needs to work in the normal screen proportions, regardless of how it looks when you post it here. Scrolling is OK, but the first impression needs to work.
Updates

Keep in mind that there will be about 250 words, or more, on each page.

Competitors web sites:

http://www.brindlecovedentist.example/

http://www.brindlecovedentalcare.example/

http://www.grinsbymarlowvaledental.example/

http://www.tenbyfamilydentalcare.example/

http://www.quelmardental.example/

http://www.dovrinadental.example/

We need to compete with these.

Target Market(s)

Generally adults seeking the most experienced and comfortable-to-be-with dentist.

Industry/Entity Type

Training

Requirements
Must have
• Must stand apart from other dentists.
• Must be elegant.
• Must have a horizontal menu structure across all columns, NOT a vertical that requires scrolling, no popout, pop down, etc. menus.
• We are looking for something special.
• Do not waste your time or ours putting up templates and things you have used before.
• Personally, I do not see how someone outside the US can understand the northern California dental market. But you are welcome to try.
Should not have
• Flash or graphics that move
• The look of a template
• Folksy fonts
• Looks like you used it 20 times before

```html
<!DOCTYPE html>
<html lang="en">
<head>
<meta charset="utf-8">
<title>Dentist website design</title>
<link rel="stylesheet" href="https://fonts.googleapis.com/css2?family=Open+Sans:wght@400;600;700&display=swap">
<style>
:root{
  --red:#a8191d;
  --red-dark:#7f1a1c;
  --red-bright:#c8161c;
  --paper:#f3f3f3;
  --white:#ffffff;
  --ink:#333333;
  --tab:#f1eeee;
  --tab-line:#dcd6d6;
  --photo-a:#d9c2b0;
  --photo-b:#8fa9a4;
}
*{box-sizing:border-box;margin:0;padding:0}
html,body{width:1200px;height:900px;overflow:hidden;background:var(--white);font-family:"Open Sans",Verdana,sans-serif;color:var(--ink)}
.canvas{position:relative;width:1200px;height:900px}
.screen{position:absolute;background:var(--paper);border-top:4px solid var(--red)}
.screen--inner{left:28px;top:28px;width:917px;height:762px}
.screen--home{left:350px;top:383px;width:850px;height:517px;box-shadow:-6px 0 18px rgba(0,0,0,.18);z-index:2}
.abs{position:absolute}
.brand{display:flex;align-items:center;gap:10px;font-size:22px;font-weight:600;color:#444}
.brand__mark{width:24px;height:24px;border-radius:50%;background:var(--red)}
.search{height:17px;border:1px solid #cfc8c8;background:linear-gradient(#fff,#f3e9e9);font-size:10px;color:#888;padding:1px 7px;display:flex;justify-content:space-between;align-items:center}
.tools{display:flex;align-items:flex-end;gap:10px;color:#777}
.tools .sizes{font-size:10px}
.tools .sizes b{font-weight:400;font-size:12px}
.tools .sizes big{font-size:15px}
.tabs{display:flex;gap:3px;align-items:flex-end}
.tab{height:25px;padding:0 11px;background:linear-gradient(#fff,var(--tab));border:1px solid var(--tab-line);border-bottom:none;font-size:12px;color:#444;display:flex;align-items:center}
.tab--active{height:29px;background:var(--red);color:#fff;font-weight:600;border-color:var(--red)}
.photo{background:linear-gradient(135deg,var(--photo-a),#efe4da 45%,var(--photo-b))}
.band{background:var(--red-dark)}
.sidebar{background:var(--red);color:#fff}
.sidebar h3{font-size:12px;font-weight:700;margin:0 0 12px 11px}
.sidenav{list-style:none;font-size:11px}
.sidenav li{height:18px;display:flex;align-items:center;padding-left:11px}
.sidenav li::before{content:"";border:4px solid transparent;border-left:6px solid currentColor;margin-right:10px}
.sidenav .sub{background:linear-gradient(90deg,#f7f3f3,#fff);color:#333;padding-left:30px;margin:0 8px 0 5px}
.sidenav .sub.selected{color:var(--red-bright)}
.main{background:var(--white)}
.crumbs{display:flex;font-size:10px}
.crumb{height:19px;display:flex;align-items:center;padding:0 26px 0 14px;background:#e4e4e4;clip-path:polygon(0 0,calc(100% - 9px) 0,100% 50%,calc(100% - 9px) 100%,0 100%);margin-right:-6px}
.crumb--parent{background:#f0f0f0;padding-left:22px}
.crumb--current{background:var(--red-bright);color:#fff;padding-left:22px}
.page-title{font-size:17px;font-weight:400;color:#222}
.page-title em{font-style:normal;color:var(--red-bright)}
.copy{font-size:11px;line-height:20px;color:#444}
.footer{font-size:9px;color:#777;display:flex;gap:20px;white-space:nowrap}
.footer a{color:#777}
.hero{background:radial-gradient(ellipse at 70% 80%,var(--red-bright),var(--red) 70%);color:#fff}
.hero h2{font-size:20px;font-weight:400;margin-bottom:8px}
.hero p{font-size:10px;line-height:15px}
.news h4{font-size:11px;font-weight:700;margin-bottom:3px}
.news p{font-size:10px;line-height:15px}
.news-more{display:block;text-align:right;color:#fff;text-decoration:underline;font-size:10px;margin:1px 0 4px}
.card{background:#fff;box-shadow:0 3px 8px rgba(0,0,0,.25);border-radius:3px;padding:8px 11px}
.card h3{font-size:15px;font-weight:400;line-height:19px;color:#222}
.card h3 em{font-style:normal;color:var(--red-bright);display:block}
.card p{font-size:10px;line-height:14px;color:#666;margin-top:5px}
.card a{position:absolute;right:15px;bottom:5px;font-size:10px;color:#333}
.tagline{font-size:11px;line-height:15px;color:#888}
</style>
</head>
<body>
<div class="canvas">

  <section class="screen screen--inner">
    <div class="abs brand" style="left:24px;top:68px"><span class="brand__mark"></span>Dentist logo title</div>
    <div class="abs search" style="left:677px;top:40px;width:132px"><span>Search...</span><span>&#9906;</span></div>
    <div class="abs tools" style="left:825px;top:40px"><svg width="14" height="12" viewBox="0 0 14 12"><rect x="3" y="0" width="8" height="4" fill="#bbb"/><rect x="0" y="4" width="14" height="6" fill="#999"/><rect x="3" y="8" width="8" height="4" fill="#ddd"/></svg><span class="sizes">a <b>a</b> <big>a</big></span></div>
    <nav class="abs tabs" style="left:235px;top:103px">
      <span class="tab tab--active">Home</span><span class="tab">Item 2</span><span class="tab">Item 3</span><span class="tab">Item 4</span><span class="tab">item 5</span><span class="tab">item 6</span><span class="tab">item7</span><span class="tab">item 8</span>
    </nav>
    <div class="abs band" style="left:27px;top:132px;width:863px;height:41px"></div>
    <aside class="abs sidebar" style="left:27px;top:173px;width:210px;height:515px">
      <div class="photo" role="img" aria-label="Photo of a dental assistant treating a patient" style="margin:2px 0 0 3px;width:193px;height:131px;border:2px solid #fff"></div>
      <h3 style="margin-top:16px">Section title goes here</h3>
      <ul class="sidenav">
        <li>Menu title goes here</li><li>Menu title goes here</li><li>Menu title goes here</li><li>Menu title goes here</li>
        <li class="sub">Menu title goes here</li><li class="sub selected">Menu selected title</li><li class="sub">Menu title goes here</li>
        <li>Menu title goes here</li><li>Menu title goes here</li><li>Menu title goes here</li>
      </ul>
    </aside>
    <main class="abs main" style="left:237px;top:173px;width:653px;height:515px">
      <div class="abs crumbs" style="left:13px;top:21px"><span class="crumb">Home</span><span class="crumb crumb--parent" style="padding-right:30px">Parent page title</span><span class="crumb crumb--current">Current page title</span></div>
      <h1 class="abs page-title" style="left:14px;top:66px">State-of-the-art <em>dental care</em> page title goes here</h1>
      <div class="abs copy" style="left:15px;top:96px;width:600px">
        <p>Lorem ipsum dolor sit amet, consectetur adipiscing elit. Etiam consectetur velit in nisi sodales in pellentesque odio scelerisque. Vestibulum et velit id risus rutrum molestie. Phasellus vulputate est in tellus elementum eu vulputate neque tincidunt. Fusce et pretium urna. Morbi bibendum elementum ultrices. Curabitur porttitor laoreet nisi sed posuere. Suspendisse potenti. Curabitur porta varius tempus. Ut molestie mattis lacinia. Vivamus convallis elit id ante mattis et semper mi cursus. Fusce gravida dapibus enim, nec egestas enim malesuada quis. Nam facilisis vitae lorem. Integer cing a suscipit.</p>
        <p style="margin-top:20px">In dictum hendrerit ante, nec elementum nisi tempor sed. Duis semper odio id turpis interdum, id turpis interdum rit vehicula tellus. Donec tetur id sollicitudin nibh auctor pellentesque.</p>
        <p style="margin-top:20px">Aliquam quam metus, sit amet placerat ligula euismod mollis ac nunc.</p>
      </div>
    </main>
    <footer class="abs footer" style="left:35px;top:716px"><span>(c) Copyright 2010 Companyname.</span><a href="#" style="margin-left:45px">home</a><span>|</span><a href="#">contact</a></footer>
  </section>

  <section class="screen screen--home">
    <div class="abs brand" style="left:33px;top:48px"><span class="brand__mark"></span>Dentist logo title</div>
    <div class="abs search" style="left:635px;top:38px;width:132px"><span>Search...</span><span>&#9906;</span></div>
    <div class="abs tools" style="left:773px;top:38px"><svg width="14" height="12" viewBox="0 0 14 12"><rect x="3" y="0" width="8" height="4" fill="#bbb"/><rect x="0" y="4" width="14" height="6" fill="#999"/><rect x="3" y="8" width="8" height="4" fill="#ddd"/></svg><span class="sizes">a <b>a</b> <big>a</big></span></div>
    <nav class="abs tabs" style="left:226px;top:96px">
      <span class="tab tab--active">Home</span><span class="tab">Item 2</span><span class="tab">Item 3</span><span class="tab">Item 4</span><span class="tab">Item 5</span><span class="tab">item 6</span><span class="tab">item7</span><span class="tab">item 8</span>
    </nav>
    <div class="abs photo" role="img" aria-label="Photo of a patient receiving a dental check-up" style="left:34px;top:125px;width:192px;height:223px"></div>
    <div class="abs hero" style="left:226px;top:123px;width:607px;height:225px">
      <div class="abs" style="left:17px;top:16px;width:320px">
        <h2>Lorem ipsum dolar sit</h2>
        <p>Lorem ipsum dolor sit amet, consectetur adipiscing elit. Etiam consectetur velit in nisi sodales in pellentesque odio scelerisque. Vestibulum et velit id risus rutrum molestie. Phasellus vulputate est in tellus elementum eu vulputate neque tincidunt. Fusce et pretium urna. Morbi bibendum elementum ultrices. Curabitur porttitor laoreet nisi sed posuere. Suspendisse potenti. Curabitur porta varius tempus. Ut molestie mattis lacinia.<br>Vivamus convallis elit id ante mattis et semper mi cursus. Fusce gravida dapibus enim, nec egestas enim malesuada quis.</p>
      </div>
      <div class="abs news" style="left:354px;top:16px;width:230px">
        <h2 style="font-size:20px;font-weight:400;margin-bottom:8px">Latest news</h2>
        <h4>News item title 1</h4>
        <p>Lorem Ipsum is slechts een proeftekst uit het drukkerij- en zetterijwezen. Lorem Ipsum is de standaard proeftekst in deze bedrijfstak</p>
        <a class="news-more" href="#">read more</a>
        <h4>Another news item title 2</h4>
        <p>Sinds de 16e eeuw, toen een onbekende drukker een zethaak met letters nam en ze door elkaar husselde om een font-catalogus te maken.</p>
        <a class="news-more" href="#">read more</a>
      </div>
    </div>
    <p class="abs tagline" style="left:42px;top:376px;width:190px">We use our education, experience and dedication to provide every patient with superior dental care</p>
    <article class="abs card" style="left:242px;top:335px;width:183px;height:100px"><h3>We provide <em>high quality</em></h3><p>Lorem ipsum dolor sit amet, con sectetur adipiscing elit.</p><a href="#">read more</a></article>
    <article class="abs card" style="left:442px;top:335px;width:183px;height:100px"><h3>State-of-the-art <em>dental care</em></h3><p>Etiam consectetur velit in nisi soda les in pellentesque odio.</p><a href="#">read more</a></article>
    <article class="abs card" style="left:642px;top:335px;width:183px;height:100px"><h3>Comfortable <em>caring environment</em></h3><p>Etiam consectetur velit in nisi sodal in pellentesque odio.</p><a href="#">read more</a></article>
    <footer class="abs footer" style="left:42px;top:483px"><span>(c) Copyright 2010 Companyname.</span><a href="#" style="margin-left:40px">home</a><span>|</span><a href="#">contact</a><span>|</span><a href="#">privacy verklaring</a><span>|</span><a href="#">sitemap</a></footer>
    <div class="abs footer" style="left:640px;top:483px;gap:14px"><span>&#9742; 555 0100 200</span><span>info@clinic.example</span></div>
  </section>

</div>
</body>
</html>
```